Event flyer for Sunday night Youth Group

Need a 4 x 6 or 5 x 7 flyer for a new youth group starting on April 14. The youth group is for students in middle school and high school so it needs to look fun and cool, but not childish. I prefer it not to include pictures of people unless it's so obscure you can't really see their faces. I've uploaded some pictures of flyers I like. I've also attached a couple versions of our logo to use on the flyer.
Information the flyer needs to include:
Youth Group
Sundays, 6-8pm (beginning April 14)
Location: Marlowe's - 4219 Quarry Fern Ave N, Alder Bend, 97318
There will be dinner, games, friends, and a message.
Target Market(s)
Youth ages 13-18
Industry/Entity Type
Church
Font styles to use
Colors
Designer to choose colors to be used in the design.
Look and feel

```html
<!DOCTYPE html>
<html lang="en">
<head>
<meta charset="utf-8">
<title>Sundays Youth Group Flyer</title>
<link href="https://fonts.googleapis.com/css2?family=Archivo+Black&family=Kaushan+Script&family=Montserrat:wght@500;600;700;800&display=swap" rel="stylesheet">
<style>
  :root {
    --canvas-bg: #d9dae6;
    --flyer-deep: #1c1048;
    --flyer-mid: #3a2178;
    --flyer-glow: #8a64c9;
    --ray-pink: #d04ee0;
    --ray-cyan: #3ad2f0;
    --accent-cyan: #3ec6e8;
    --badge-cyan: #2bb8e6;
    --text-white: #ffffff;
    --shadow-black: #0b0614;
    --divider: rgba(255,255,255,0.75);
  }
  * { margin: 0; padding: 0; box-sizing: border-box; }
  html, body {
    width: 1200px; height: 900px; overflow: hidden;
    background: var(--canvas-bg);
  }
  .flyer {
    position: absolute; left: 310px; top: 44px;
    width: 580px; height: 812px; overflow: hidden;
    background: linear-gradient(180deg, var(--flyer-deep) 0%, var(--flyer-mid) 45%, #2b1866 75%, var(--flyer-deep) 100%);
    box-shadow: 0 18px 40px rgba(20,10,50,0.35);
    font-family: "Montserrat", sans-serif;
    color: var(--text-white);
    text-align: center;
  }
  .stage-lights {
    position: absolute; inset: 0 0 auto 0; height: 520px;
    background:
      radial-gradient(ellipse 55% 40% at 50% 62%, rgba(190,160,240,0.55), transparent 70%),
      radial-gradient(ellipse 30% 45% at 18% 10%, rgba(208,78,224,0.45), transparent 70%),
      radial-gradient(ellipse 30% 45% at 82% 10%, rgba(58,210,240,0.4), transparent 70%),
      radial-gradient(ellipse 40% 30% at 50% 0%, rgba(120,90,220,0.6), transparent 75%);
  }
  .crowd-glow {
    position: absolute; left: 0; right: 0; bottom: 0; height: 300px;
    background: linear-gradient(180deg, transparent 0%, rgba(60,30,110,0.6) 40%, rgba(20,10,45,0.9) 100%);
  }
  .brand {
    position: absolute; top: 62px; left: 0; right: 0;
    display: flex; flex-direction: column; align-items: center; gap: 14px;
  }
  .brand-dot {
    width: 46px; height: 46px; border-radius: 50%;
    background: var(--text-white);
  }
  .brand-name {
    font-weight: 600; font-size: 22px; letter-spacing: 3px;
    color: var(--text-white); line-height: 1.25;
  }
  .title-script {
    position: absolute; top: 218px; left: 0; right: 0;
    font-family: "Kaushan Script", "Yellowtail", cursive;
    font-size: 84px; line-height: 1; color: var(--accent-cyan);
    transform: rotate(-8deg); z-index: 2;
  }
  .title-main {
    position: absolute; top: 300px; left: 0; right: 0;
    font-family: "Archivo Black", sans-serif;
    font-size: 100px; line-height: 1.1; letter-spacing: -2px;
    transform: rotate(-6deg) scaleX(1.18);
    text-shadow: 6px 5px 0 var(--shadow-black);
    z-index: 1;
  }
  .title-sub {
    position: absolute; top: 408px; left: 0; right: 0;
    font-family: "Archivo Black", sans-serif;
    font-size: 48px; line-height: 1.1; letter-spacing: 2px;
    transform: rotate(-6deg) scaleX(1.25);
  }
  .event-date {
    position: absolute; top: 500px; left: 0; right: 0;
    font-weight: 800; font-size: 50px; letter-spacing: 1px;
    transform: rotate(-6deg);
  }
  .event-time {
    position: absolute; top: 568px; left: 50%;
    transform: translateX(-50%) rotate(-6deg);
    background: var(--badge-cyan);
    font-weight: 800; font-size: 24px; letter-spacing: 1px;
    padding: 4px 16px; white-space: nowrap;
  }
  .event-venue {
    position: absolute; top: 622px; left: 0; right: 0;
    font-weight: 500; font-size: 19px; line-height: 1.3;
    transform: rotate(-6deg);
  }
  .offer-icons {
    position: absolute; top: 688px; left: 50%;
    transform: translateX(-50%) rotate(-6deg);
    display: flex; align-items: center; gap: 18px;
  }
  .offer-icons svg { width: 50px; height: 50px; stroke: var(--accent-cyan); fill: none; stroke-width: 2.4; stroke-linecap: round; stroke-linejoin: round; }
  .icon-divider { width: 1.5px; height: 64px; background: var(--divider); }
  .tagline {
    position: absolute; top: 764px; left: 0; right: 0;
    font-weight: 500; font-size: 16px;
    transform: rotate(-6deg);
  }
</style>
</head>
<body>
  <main class="flyer">
    <div class="stage-lights" role="img" aria-label="Colourful stage light beams over a softly lit worship hall"></div>
    <div class="crowd-glow" role="img" aria-label="Dim crowd silhouettes at a concert"></div>

    <header class="brand">
      <span class="brand-dot"></span>
      <span class="brand-name">HARBORLIGHT<br>FELLOWSHIP</span>
    </header>

    <h1>
      <span class="title-script">Sundays</span>
      <span class="title-main">YOUTH</span>
      <span class="title-sub">GROUP</span>
    </h1>

    <p class="event-date">APRIL 14</p>
    <p class="event-time">SUNDAYS, 6-8PM</p>
    <p class="event-venue">Marlowe's - 4219 Quarry Fern Ave N,<br>Alder Bend, 97318</p>

    <div class="offer-icons">
      <svg viewBox="0 0 50 50" aria-label="Dinner"><circle cx="25" cy="25" r="21"/><circle cx="25" cy="25" r="14"/><path d="M19 15v20M16 15v6a3 3 0 0 0 6 0v-6M31 15c-3 3-3 9 0 11v9"/></svg>
      <span class="icon-divider"></span>
      <svg viewBox="0 0 50 50" aria-label="Games"><path d="M14 16h22c6 0 9 8 9 16 0 5-4 7-7 4l-5-5H17l-5 5c-3 3-7 1-7-4 0-8 3-16 9-16z"/><path d="M15 21v7M11.5 24.5h7"/><circle cx="33" cy="22" r="1.6"/><circle cx="37" cy="26" r="1.6"/></svg>
      <span class="icon-divider"></span>
      <svg viewBox="0 0 50 50" aria-label="Friends"><circle cx="17" cy="17" r="5"/><circle cx="33" cy="17" r="5"/><path d="M8 40v-6a9 9 0 0 1 18 0v6M24 40v-6a9 9 0 0 1 18 0v6"/></svg>
      <span class="icon-divider"></span>
      <svg viewBox="0 0 50 50" aria-label="Message"><path d="M5 12h28v18H16l-7 6v-6H5z"/><path d="M37 18h8v16h-4v5l-6-5H21"/><path d="M11 18h16M11 24h12"/></svg>
    </div>

    <p class="tagline">There will be dinner, games, friends, and a message.</p>
  </main>
</body>
</html>
```